Building company buisness cards

We are looking for a sharp modern new look for our business cards.
We are a New Zealand based company that specialises in house and land packages.
We have attached a photo of the current logo and would like to see if it can be improved somehow if needed.
We are open to any colours but we have chosen green at this stage.
Feel free to change the font and make the logo smarter looking.
Play with the colours and see what looks best.

We want a card that looks so good know one will want to throw it away!

Target Market(s)

Home buyers

Industry/Entity Type

Building

Contact Information for Business Card

Derek Tolvane
0217394062
dtolvane@quillmarkhomesteads.co.nz
quillmarkhomesteads.co.nz

Font styles to use
Serif
Sans Serif

Colors

Designer to choose colors to be used in the design.

Requirements
Must have
• Logo and company name on one side, details on the other side
Nice to have
• Color codes for the original green are HEX #4a8028, RGB(74,128,40), CMYK(42,0,69,50)
• Round corners, Raised and/or spot UV

```html
<!DOCTYPE html>
<html lang="en">
<head>
<meta charset="utf-8">
<title>Quillmark Homesteads – Business Cards</title>
<link rel="stylesheet" href="https://fonts.googleapis.com/css2?family=Montserrat:wght@800&family=Open+Sans:wght@400;600&family=Arimo:wght@400;700&display=swap">
<style>
  :root {
    --backdrop: #1c1c1c;
    --card: #030303;
    --green: #4a8028;
    --green-bright: #4f9a2a;
    --white: #f2f2f2;
  }
  * { margin: 0; padding: 0; box-sizing: border-box; }
  html, body {
    width: 1200px;
    height: 960px;
    overflow: hidden;
    background: var(--backdrop);
  }
  .canvas {
    position: relative;
    width: 1200px;
    height: 960px;
  }
  .card {
    position: absolute;
    width: 520px;
    height: 298px;
    background: var(--card);
    border-radius: 6px;
    box-shadow: 0 18px 40px rgba(0,0,0,0.55);
  }
  /* Front: company name side */
  .card--front { left: 600px; top: 150px; }
  .brand {
    position: absolute;
    left: 0; right: 0; top: 92px;
    text-align: center;
    font-family: "Montserrat", sans-serif;
    font-weight: 800;
    color: var(--green-bright);
    font-size: 34px;
    line-height: 1.02;
    letter-spacing: -0.5px;
  }
  .brand__mark {
    display: block;
    width: 14px; height: 14px;
    margin: 0 auto 12px;
    background: var(--green-bright);
  }
  .front__rule {
    position: absolute;
    left: 205px; top: 196px;
    width: 110px; height: 1px;
    background: var(--green-bright);
  }
  .front__web {
    position: absolute;
    left: 0; right: 0; top: 214px;
    text-align: center;
    font-family: "Open Sans", sans-serif;
    font-size: 14px;
    letter-spacing: 1.2px;
    color: var(--white);
  }
  .front__web .domain { color: var(--green-bright); }

  /* Back: contact side */
  .card--back { left: 90px; top: 500px; }
  .contact {
    position: absolute;
    left: 0; right: 0; top: 70px;
    text-align: center;
  }
  .contact__name {
    font-family: "Arimo", sans-serif;
    font-size: 19px;
    color: var(--green-bright);
  }
  .contact__title {
    font-family: "Arimo", sans-serif;
    font-weight: 700;
    font-size: 17px;
    color: var(--white);
    margin-top: 2px;
  }
  .contact__rule {
    width: 64px; height: 1px;
    margin: 10px auto 14px;
    background: var(--green-bright);
  }
  .contact__list {
    list-style: none;
    display: inline-block;
    text-align: left;
    font-family: "Open Sans", sans-serif;
    font-size: 15px;
    color: var(--white);
  }
  .contact__list li {
    display: flex;
    align-items: center;
    gap: 8px;
    line-height: 24px;
  }
  .contact__list li.phone { justify-content: center; }
  .icon { width: 12px; height: 12px; flex: none; }
</style>
</head>
<body>
<main class="canvas">

  <section class="card card--front" aria-label="Card front">
    <div class="brand">
      <span class="brand__mark"></span>
      quillmark<br>homesteads.
    </div>
    <div class="front__rule"></div>
    <p class="front__web">www.<span class="domain">quillmarkhomesteads</span>.co.nz</p>
  </section>

  <section class="card card--back" aria-label="Card back">
    <div class="contact">
      <p class="contact__name">Derek Tolvane</p>
      <p class="contact__title">Title</p>
      <div class="contact__rule"></div>
      <ul class="contact__list">
        <li class="phone">
          <svg class="icon" viewBox="0 0 12 12" aria-hidden="true"><path d="M2.5 1 L4.5 1 L5.2 3.6 L4 4.6 Q5 7 7.4 8 L8.4 6.8 L11 7.5 L11 9.5 Q11 11 9.5 11 Q1 10 1 2.5 Q1 1 2.5 1 Z" fill="none" stroke="#f2f2f2" stroke-width="0.9"/></svg>
          0217394062
        </li>
        <li>
          <svg class="icon" viewBox="0 0 12 12" aria-hidden="true"><circle cx="6" cy="6" r="6" fill="#4f9a2a"/><rect x="2.8" y="3.8" width="6.4" height="4.4" fill="none" stroke="#030303" stroke-width="0.9"/><path d="M2.8 3.8 L6 6.4 L9.2 3.8" fill="none" stroke="#030303" stroke-width="0.9"/></svg>
          dtolvane@quillmarkhomesteads.co.nz
        </li>
        <li>
          <svg class="icon" viewBox="0 0 12 12" aria-hidden="true"><circle cx="6" cy="6" r="6" fill="#4f9a2a"/><circle cx="6" cy="6" r="3.4" fill="none" stroke="#030303" stroke-width="0.8"/><ellipse cx="6" cy="6" rx="1.5" ry="3.4" fill="none" stroke="#030303" stroke-width="0.8"/><path d="M2.6 6 H9.4" stroke="#030303" stroke-width="0.8"/></svg>
          www.quillmarkhomesteads.co.nz
        </li>
      </ul>
    </div>
  </section>

</main>
</body>
</html>
```